Private Investment Firm Needs PowerPoint Presentation Template

Design PowerPoint template, take Pinebrook-submitted rough presentation draft, and drop it into new template. See attached Project Brief file for more detail.
Updates

Some decent designs have been submitted but they seem to lack the understanding of our target markets. I am hopeful that more time and feedback will result in better results.

Target Market(s)

Private company owners and intermediaries.

Font styles to use
Serif

Colors
3176b5

Requirements
Must have
• See attached Project Brief.
Nice to have
Should not have
• No B2C fluff--this is a B2B project.

```html
<!DOCTYPE html>
<html lang="en">
<head>
<meta charset="utf-8">
<title>Non-Control Capital Questionnaire</title>
<link href="https://fonts.googleapis.com/css2?family=Montserrat:wght@600;700&family=Raleway:wght@400;500;600&family=Libre+Baskerville&display=swap" rel="stylesheet">
<style>
  :root {
    --brand: #1a72c0;
    --brand-dark: #0e4f8f;
    --brand-soft: #3176b5;
    --ink: #454a50;
    --paper: #ffffff;
    --shadow: rgba(20, 40, 70, 0.16);
  }
  * { box-sizing: border-box; margin: 0; padding: 0; }
  html, body { width: 1200px; height: 676px; overflow: hidden; background: var(--paper); }
  .slide { position: relative; width: 1200px; height: 676px; overflow: hidden; background: var(--paper); font-family: "Raleway", sans-serif; }
  .side-band { position: absolute; left: 0; top: 0; width: 44px; height: 676px; background: var(--brand); }
  .edge-band { position: absolute; right: 0; top: 0; width: 11px; height: 676px; background: var(--brand); }
  .site-url { position: absolute; left: 22px; top: 336px; transform: translate(-50%, -50%) rotate(-90deg); font-family: "Libre Baskerville", serif; font-size: 13px; color: var(--brand); white-space: nowrap; }
  .page-number { position: absolute; right: 21px; top: 18px; font-family: "Libre Baskerville", serif; font-size: 17px; color: #222; }
  .slide-title { position: absolute; left: 86px; top: 82px; font-family: "Montserrat", sans-serif; font-weight: 700; font-size: 29px; color: var(--brand); letter-spacing: 0.3px; }
  .title-band { position: absolute; left: 44px; top: 136px; width: 1145px; height: 42px; background: var(--brand); }
  .title-band h2 { position: absolute; left: 42px; top: 4px; font-family: "Montserrat", sans-serif; font-weight: 700; font-size: 28px; color: #fff; white-space: nowrap; letter-spacing: 0.2px; }
  .subtitle { position: absolute; left: 86px; top: 186px; font-family: "Montserrat", sans-serif; font-weight: 600; font-size: 16.6px; color: var(--brand); white-space: nowrap; }
  .backdrop { position: absolute; left: 472px; top: 470px; width: 717px; height: 206px; background: linear-gradient(160deg, rgba(255,255,255,0) 10%, #eef1f3 45%, #d9dfe3 75%, #c6cfd4 100%); }
  .card { position: absolute; background: #fff; border-radius: 48px 0 48px 0; box-shadow: 0 4px 16px var(--shadow); }
  .card-1 { left: 80px; top: 300px; width: 344px; height: 218px; }
  .card-2 { left: 446px; top: 300px; width: 344px; height: 218px; }
  .card-3 { left: 806px; top: 300px; width: 344px; height: 318px; }
  .ribbon { position: absolute; width: 126px; height: 92px; }
  .ribbon-label { position: absolute; left: 0; width: 110px; text-align: center; color: #fff; font-family: "Raleway", sans-serif; }
  .ribbon-label .kicker { display: block; margin-top: 6px; font-size: 15px; font-weight: 500; letter-spacing: 0.3px; }
  .ribbon-label .num { display: block; margin-top: -4px; font-size: 37px; font-weight: 500; line-height: 1.05; }
  .question { position: absolute; font-size: 15.2px; line-height: 15.8px; color: var(--brand); white-space: nowrap; }
  .question u { font-weight: 700; text-decoration-thickness: 1px; text-underline-offset: 2px; }
  .points { position: absolute; list-style: none; }
  .points li { position: relative; padding-left: 15px; font-size: 11.9px; line-height: 15.6px; color: var(--ink); white-space: nowrap; }
  .points li::before { content: ""; position: absolute; left: 0; top: 4px; width: 8px; height: 8px; background: var(--brand); border-radius: 1px; }
  .points .lead { color: var(--brand); }
  .brand { position: absolute; left: 66px; top: 612px; display: flex; align-items: center; gap: 10px; }
  .brand-dot { width: 40px; height: 40px; border-radius: 50%; background: var(--brand); }
  .brand-name { font-family: "Raleway", sans-serif; font-weight: 600; font-size: 17px; letter-spacing: 1.5px; color: var(--brand-dark); text-transform: uppercase; line-height: 1.1; }
</style>
</head>
<body>
<div class="slide">
  <div class="side-band"></div>
  <div class="edge-band"></div>
  <div class="site-url">www.pinebrookcapital.com</div>
  <div class="page-number">24</div>

  <h1 class="slide-title">NON-CONTROL CAPITAL QUESTIONNAIRE</h1>
  <div class="title-band"><h2>The Critical Questions to Ask of Any Prospective Non-Control Investor</h2></div>
  <p class="subtitle">Non-Control Capital is a specialty, so only those firms with deep experience investing it as a team should be considered</p>

  <div class="backdrop" role="img" aria-label="Soft photograph of white modern architecture fading into the slide"></div>

  <!-- Question 04 -->
  <div class="card card-1"></div>
  <svg class="ribbon" style="left:278px;top:282px" viewBox="0 0 126 92" aria-hidden="true">
    <polygon points="0,18 18,0 18,18" fill="var(--brand-dark)"/>
    <polygon points="18,0 126,0 126,86 18,78" fill="var(--brand)"/>
  </svg>
  <div class="ribbon-label" style="left:296px;top:282px"><span class="kicker">QUESTION</span><span class="num">04</span></div>
  <p class="question" style="left:117px;top:336px">What is the number of<br>Non-Control Capital in-<br>vestments made with<br>the <u>current firm and</u></p>
  <ul class="points" style="left:103px;top:425px">
    <li><span class="lead">Best Answer:</span> 20+</li>
    <li>Indicates long-term experience and comfort<br>with current team, investment committee, and<br>NCC investment assessment.</li>
  </ul>

  <!-- Question 05 -->
  <div class="card card-2"></div>
  <svg class="ribbon" style="left:645px;top:282px" viewBox="0 0 126 92" aria-hidden="true">
    <polygon points="0,18 18,0 18,18" fill="var(--brand-dark)"/>
    <polygon points="18,0 126,0 126,86 18,78" fill="var(--brand)"/>
  </svg>
  <div class="ribbon-label" style="left:663px;top:282px"><span class="kicker">QUESTION</span><span class="num">05</span></div>
  <p class="question" style="left:484px;top:317px">What percentage of<br>portfolio investments<br>made are “sponsor-<br>less” (those without a<br>change-of-control in-</p>
  <ul class="points" style="left:470px;top:408px">
    <li><span class="lead">Best Answer:</span> 80%+ of all investments closed<br>in the last 5 years (assumes current transac-<br>tion is also sponsorless)</li>
    <li>Indicates ability to add-value as a sole minority<br>investor and not simply as a back-up to anoth-<br>er sponsor.</li>
  </ul>

  <!-- Question 06 -->
  <div class="card card-3"></div>
  <svg class="ribbon" style="left:1005px;top:282px" viewBox="0 0 126 92" aria-hidden="true">
    <polygon points="0,18 18,0 18,18" fill="var(--brand-dark)"/>
    <polygon points="18,0 126,0 126,86 18,78" fill="var(--brand)"/>
  </svg>
  <div class="ribbon-label" style="left:1023px;top:282px"><span class="kicker">QUESTION</span><span class="num">06</span></div>
  <p class="question" style="left:844px;top:331px">Can the investor show<br><u>quantifiable proof</u> of<br>their ability to assist<br>portfolio companies with growth and<br>improvement (assumes more than 20<br><u>exited</u> Non-Control investments)?</p>
  <ul class="points" style="left:830px;top:437px">
    <li><span class="lead">Best Answer:</span> Yes (company owners should<br>evaluate investors on actual historical reve-<br>nue, EBITDA, and employee growth impact<br>and the results should exceed what the cur-<br>rent management has achieved on their own<br>over the past 3 years)</li>
    <li>Indicates true value-added ability to help<br>owners grow their businesses. Those without<br>proof of their impact, or who are unwilling to<br>disclose it, should be excluded.</li>
  </ul>

  <div class="brand">
    <div class="brand-dot"></div>
    <div class="brand-name">Pinebrook<br>Capital</div>
  </div>
</div>
</body>
</html>
```